Fernhale Business Card Design

We are looking for a fresh business card design for our new logo. We would like a business card that is unique but friendly. We are in the window coverings business offering blinds, shutters and shades for homes.

Target Market(s)

Targeting the end-consumer

Industry/Entity Type

Business

Requirements
Must have
• Must have a dedicates space for a photo of our sales person. Must contain our new logo (attached).

```html
<!DOCTYPE html>
<html lang="en">
<head>
<meta charset="utf-8">
<title>Fernhale Business Card</title>
<link href="https://fonts.googleapis.com/css2?family=Roboto:wght@300;400;700&family=Roboto+Condensed:wght@400;700&display=swap" rel="stylesheet">
<style>
  :root {
    --bg: #e9e6e1;
    --card-white: #fbfbfa;
    --card-grey: #8a8b8d;
    --grey-dark: #7b7c7e;
    --grey-text: #6d6e70;
    --green: #7ac143;
    --photo-tone: #f2f2f2;
  }
  * { margin: 0; padding: 0; box-sizing: border-box; }
  html, body { width: 1200px; height: 886px; overflow: hidden; background: var(--bg); }
  .stage { position: relative; width: 1200px; height: 886px; }

  .card { position: absolute; box-shadow: 0 6px 18px rgba(0,0,0,0.18); overflow: hidden; }

  /* Front */
  .card-front { left: 70px; top: 273px; width: 580px; height: 340px; background: var(--card-white); }
  .brand-block { position: absolute; right: 60px; top: 40px; width: 130px; height: 130px; background: var(--green); border-radius: 6px; }
  .identity { position: absolute; left: 0; top: 150px; }
  .identity-bar { position: absolute; left: 0; top: 2px; width: 24px; height: 34px; background: var(--green); }
  .person-name { position: absolute; left: 40px; top: 0; font: 700 20px "Roboto Condensed", sans-serif; color: var(--green); letter-spacing: 0.5px; white-space: nowrap; }
  .person-title { position: absolute; left: 40px; top: 24px; font: 400 14px "Roboto Condensed", sans-serif; color: var(--grey-text); white-space: nowrap; }
  .details { position: absolute; left: 40px; top: 218px; font: 400 13px/17px "Roboto Condensed", sans-serif; color: var(--grey-text); }
  .details .address { margin-bottom: 8px; }
  .detail-line { display: flex; align-items: center; gap: 8px; }
  .detail-line svg { width: 10px; height: 10px; flex: none; }
  .wordmark-front { position: absolute; right: 40px; bottom: 30px; font: 300 54px "Roboto", sans-serif; color: var(--grey-dark); }

  /* Back */
  .card-back { left: 760px; top: 163px; width: 340px; height: 560px; background: var(--card-grey); }
  .back-brand { position: absolute; left: 34px; top: 44px; display: flex; align-items: center; gap: 12px; }
  .back-brand .mark-square { width: 30px; height: 30px; background: var(--green); }
  .back-brand .name { font: 400 34px "Roboto", sans-serif; color: #ffffff; }
  .back-url { position: absolute; left: 34px; top: 96px; font: 400 11px "Roboto", sans-serif; letter-spacing: 6px; color: #eeeeee; }
  .photo-area { position: absolute; left: 60px; top: 200px; width: 280px; height: 360px; background: linear-gradient(160deg, #ffffff, var(--photo-tone)); }
</style>
</head>
<body>
<div class="stage">
  <section class="card card-front">
    <div class="brand-block"></div>
    <div class="identity">
      <div class="identity-bar"></div>
      <div class="person-name">MARA ELLISON</div>
      <div class="person-title">CEO/FOUNDER</div>
    </div>
    <div class="details" style="top:200px">
      <div class="address">2140 Willow Bend Road<br>Larchmont Ridge 40815</div>
      <div class="detail-line">
        <svg viewBox="0 0 10 10"><path d="M2 1 L4 1 L4.5 3 L3.5 4 Q5 6 6 6.5 L7 5.5 L9 6 L9 8 Q5 9 1 3 Z" fill="var(--green)"/></svg>
        <span>614 220 3197</span></div>
      <div class="detail-line">
        <svg viewBox="0 0 10 10"><rect x="2.5" y="0.5" width="5" height="9" rx="1" fill="var(--green)"/></svg>
        <span>614 220 3198</span></div>
      <div class="detail-line">
        <svg viewBox="0 0 10 10"><rect x="1" y="3" width="8" height="5" fill="var(--green)"/><rect x="3" y="1" width="4" height="2" fill="var(--green)"/></svg>
        <span>614 220 3199</span></div>
      <div class="detail-line">
        <svg viewBox="0 0 10 10"><rect x="0.5" y="2" width="9" height="6" fill="var(--green)"/><path d="M1 2.5 L5 5.5 L9 2.5" stroke="#fff" fill="none"/></svg>
        <span>name@fernhale.com</span></div>
      <div class="detail-line">
        <svg viewBox="0 0 10 10"><circle cx="5" cy="5" r="4.5" fill="var(--green)"/></svg>
        <span>www.fernhale.com</span></div>
    </div>
    <div class="wordmark-front">Fernhale</div>
  </section>

  <section class="card card-back">
    <div class="back-brand">
      <div class="mark-square"></div>
      <div class="name">Fernhale</div>
    </div>
    <div class="back-url">www.fernhale.com</div>
    <div class="photo-area" role="img" aria-label="Space for a photo of the sales person"></div>
  </section>
</div>
</body>
</html>
```